Cafe Business needs a business card design

I already have an ai logo I would like to use and color. I need someone to make a business card for me on adobe illustrator with it. Its for a cafe restaurant opening in Japan I would like to be able to change out the names, contact info, ect on my own from adobe illustrator.

Industry/Entity Type

Business

Contact Information for Business Card

Double sided with logo on one side and info on the other. Name, Tel, fax, email and west

```html
<!DOCTYPE html>
<html lang="en">
<head>
<meta charset="utf-8">
<title>Koto Bean Cafe – Business Card</title>
<link rel="stylesheet" href="https://fonts.googleapis.com/css2?family=Open+Sans:wght@400;600;700&display=swap">
<style>
  :root {
    --backdrop: #ece7df;
    --cream-light: #fbf5ea;
    --cream: #eadcc2;
    --cream-deep: #dcc7a3;
    --brown: #4a3526;
    --brown-mid: #6b5440;
    --ink: #3a2a1e;
    --white: #ffffff;
  }
  html, body {
    margin: 0;
    padding: 0;
    width: 1200px;
    height: 913px;
    overflow: hidden;
    background: var(--backdrop);
  }
  .canvas {
    position: relative;
    width: 1200px;
    height: 913px;
    display: flex;
    align-items: center;
    justify-content: center;
    gap: 60px;
  }
  .card {
    width: 520px;
    height: 300px;
    border-radius: 14px;
    box-shadow: 0 10px 28px rgba(60, 40, 20, 0.22);
    overflow: hidden;
    display: block;
  }
  .card text { font-family: "Open Sans", Arial, sans-serif; }
  .person-name { font-size: 19px; font-weight: 600; fill: var(--ink); letter-spacing: 0.5px; }
  .person-role { font-size: 11px; font-weight: 400; fill: var(--ink); letter-spacing: 1px; }
  .contact-line { font-size: 11.5px; font-weight: 400; fill: var(--ink); }
  .brand-name { font-size: 25px; font-weight: 700; fill: var(--brown); letter-spacing: 1px; }
  .brand-name-large { font-size: 40px; font-weight: 700; fill: var(--cream); letter-spacing: 2px; }
  .contact-icon { fill: none; stroke: var(--ink); stroke-width: 1.2; }
  .contact-icon-solid { fill: var(--ink); }
</style>
</head>
<body>
<main class="canvas">

  <!-- Front: contact side -->
  <svg class="card card-front" viewBox="0 0 520 300" role="img" aria-label="Business card front with contact details">
    <defs>
      <linearGradient id="frontFace" x1="0" y1="0" x2="1" y2="1">
        <stop offset="0" stop-color="var(--cream-light)"/>
        <stop offset="1" stop-color="var(--cream)"/>
      </linearGradient>
    </defs>
    <rect class="card-face" width="520" height="300" fill="url(#frontFace)"/>
    <path class="card-band-edge" d="M0,276 H340 C368,276 370,218 398,218 H520 V300 H0 Z" fill="var(--white)"/>
    <path class="card-band" d="M0,282 H342 C372,282 374,224 402,224 H520 V300 H0 Z" fill="var(--brown)"/>

    <line class="divider" x1="130" y1="196" x2="380" y2="196" stroke="var(--cream-deep)" stroke-width="1"/>

    <rect class="brand-square" x="360" y="28" width="120" height="110" fill="var(--brown)"/>
    <text class="brand-name" x="420" y="172" text-anchor="middle">KOTO BEAN</text>
    <text class="brand-name" x="420" y="200" text-anchor="middle" style="font-size:14px;letter-spacing:6px">CAFE</text>

    <text class="person-name" x="38" y="200">DANIEL MORI</text>
    <text class="person-role" x="38" y="215">OWNER</text>

    <g class="contact-list">
      <path class="contact-icon" d="M58,225 c0,5 4,9 9,9 l1.5,-2 -2.5,-2 -1.5,1 c-1.5,-0.8 -2.7,-2 -3.5,-3.5 l1,-1.5 -2,-2.5 z"/>
      <text class="contact-line" x="74" y="234">+81 3555-0142</text>

      <rect class="contact-icon" x="58" y="239" width="9" height="8"/>
      <text class="contact-line" x="74" y="248">+81-3555-0198</text>

      <rect class="contact-icon" x="58" y="253" width="10" height="7"/>
      <path class="contact-icon" d="M58,253 l5,4 5,-4"/>
      <text class="contact-line" x="74" y="262">daniel@kotobean.jp</text>

      <circle class="contact-icon" cx="63" cy="271" r="4.5"/>
      <path class="contact-icon" d="M58.5,271 h9 M63,266.5 v9"/>
      <text class="contact-line" x="74" y="275">www.kotobeancafe.jp</text>
    </g>
  </svg>

  <!-- Back: brand side -->
  <svg class="card card-back" viewBox="0 0 520 300" role="img" aria-label="Business card back with cafe name">
    <rect class="card-face" width="520" height="300" fill="var(--white)"/>
    <path class="card-band-edge" d="M0,268 H250 C280,268 282,208 312,208 H520 V300 H0 Z" fill="var(--brown-mid)"/>
    <path class="card-band" d="M0,273 H252 C284,273 286,213 316,213 H520 V300 H0 Z" fill="var(--cream)"/>
    <text class="brand-name-large" x="260" y="140" text-anchor="middle">KOTO BEAN CAFE</text>
  </svg>

</main>
</body>
</html>
```